Business Card Design for Training Business

Clear Path Coaching is a new business that delivers training and other services with a focus on topics related to mental health and wellbeing, for example, Wellmind Response Course, Resilience etc. We have a strong focus on evidence-based psychology and neuroscience. I have a logo which I will upload with the brief, so please consider colours that work well with the logo.
Target Market(s)
Adults, workplaces (particularly government and not-for-profits)
Industry/Entity Type
Business
Contact Information for Business Card
Head Strong TrainingSamantha SellwoodDirector0438 770 850sam@headstrongtraining.com.auwww.headstrongtraining.com.au

```html
<!DOCTYPE html>
<html lang="en">
<head>
<meta charset="utf-8">
<title>Clear Path Coaching – Business Card</title>
<link href="https://fonts.googleapis.com/css2?family=Questrial&display=swap" rel="stylesheet">
<style>
  :root {
    --backdrop: #303030;
    --teal: #22b7bc;
    --teal-deep: #1fb0b5;
    --teal-soft: #bfe9ea;
    --ring-brown: #4a3f3b;
    --paper: #f8f8f8;
    --ink-light: #ffffff;
    --ink-grey: #6b6b6b;
    --ink-dark: #505050;
  }
  * { margin: 0; padding: 0; box-sizing: border-box; }
  html, body {
    width: 1200px; height: 750px; overflow: hidden;
    background: var(--backdrop);
    font-family: "Questrial", "Century Gothic", sans-serif;
  }
  .card {
    position: absolute;
    width: 461px; height: 262px;
    overflow: hidden;
    box-shadow: 0 3px 8px rgba(0,0,0,0.45);
  }
  .card--front {
    left: 371px; top: 106px;
    background: linear-gradient(180deg, var(--teal) 0%, var(--teal-deep) 100%);
  }
  .card--back {
    left: 371px; top: 387px;
    background: var(--paper);
  }
  .card-shapes { position: absolute; inset: 0; }
  .brand-name {
    position: absolute;
    color: var(--ink-grey);
    font-size: 16px;
    letter-spacing: 2px;
    text-transform: uppercase;
    white-space: nowrap;
    transform: translateX(-50%);
  }
  .card--front .brand-name { left: 353px; top: 104px; }
  .card--back .brand-name { left: 231px; top: 148px; }
  .holder-name {
    position: absolute; left: 25px; top: 146px;
    color: var(--ink-light); font-size: 18.5px; letter-spacing: 0.3px;
  }
  .holder-role {
    position: absolute; left: 24px; top: 170px;
    color: var(--ink-light); font-size: 13px;
  }
  .contact-list { position: absolute; left: 26px; top: 193px; list-style: none; }
  .contact-list li {
    display: flex; align-items: center; gap: 5px;
    height: 17.5px;
    color: var(--ink-light); font-size: 11.5px;
  }
  .contact-list svg { width: 12px; height: 12px; flex: none; }
  .back-url {
    position: absolute; left: 0; right: 0; top: 226px;
    text-align: center; color: var(--ink-dark); font-size: 12.5px;
  }
</style>
</head>
<body>

<section class="card card--front" aria-label="Business card front">
  <svg class="card-shapes" viewBox="0 0 461 262" width="461" height="262">
    <circle cx="361" cy="70" r="168" fill="var(--ring-brown)"/>
    <circle cx="361" cy="70" r="164" fill="var(--teal)"/>
    <circle cx="361" cy="70" r="159" fill="var(--paper)"/>
    <circle cx="353" cy="62" r="26" fill="var(--teal-soft)"/>
  </svg>
  <p class="brand-name">Clear Path Coaching</p>

  <p class="holder-name">Rebecca Tanfield</p>
  <p class="holder-role">Director</p>
  <ul class="contact-list">
    <li>
      <svg viewBox="0 0 12 12" aria-hidden="true"><path d="M2.5 1 L4.5 1 L5.2 3.6 L4 4.6 C4.7 6 6 7.3 7.4 8 L8.4 6.8 L11 7.5 L11 9.5 C11 10.4 10.3 11 9.5 11 C5 10.6 1.4 7 1 2.5 C1 1.7 1.6 1 2.5 1 Z" fill="#fff"/></svg>
      0491 362 517
    </li>
    <li>
      <svg viewBox="0 0 12 12" aria-hidden="true"><rect x="0.5" y="2.5" width="11" height="7.5" fill="#fff"/><path d="M0.5 2.8 L6 7 L11.5 2.8" fill="none" stroke="var(--teal)" stroke-width="1"/></svg>
      bec@clearpathcoaching.example.au
    </li>
    <li>
      <svg viewBox="0 0 12 12" aria-hidden="true"><circle cx="6" cy="6" r="5.5" fill="#fff"/><path d="M3 3.5 C4.5 3 5 4.5 4.2 5.5 C3.6 6.3 4.5 7.5 5 8.8 M7.5 2 C7 3.5 8.5 4 9.5 4.5 M8 7 C8.8 7.5 9 8.5 8.5 9.5" fill="none" stroke="var(--teal)" stroke-width="1"/></svg>
      www.clearpathcoaching.example.au
    </li>
  </ul>
</section>

<section class="card card--back" aria-label="Business card back">
  <svg class="card-shapes" viewBox="0 0 461 262" width="461" height="262">
    <circle cx="231" cy="112" r="26" fill="var(--teal-soft)"/>
  </svg>
  <p class="brand-name">Clear Path Coaching</p>
  <p class="back-url">www.clearpathcoaching.example.au</p>
</section>

</body>
</html>
```